business card deign

Logo needs the following on it.
1. attached logo
2. Tagline - "If it keeps a drink cold or the party going...we do it!"
3. Name- Dalton Pikes, Founder and CPO
4. Address - 412 E. Carver Avenue, Ste 2207, Tampa, FL. 33917
5. Phone - 555.318.4726

```html
<!DOCTYPE html>
<html lang="en">
<head>
<meta charset="utf-8">
<title>Hopwell Business Card</title>
<link href="https://fonts.googleapis.com/css2?family=Roboto:wght@400;500;700&display=swap" rel="stylesheet">
<style>
  :root {
    --backdrop: #232323;
    --card: #151515;
    --ink: #ffffff;
    --muted: #e6e6e6;
  }
  * { margin: 0; padding: 0; box-sizing: border-box; }
  html, body { width: 1200px; height: 711px; overflow: hidden; }
  body {
    background: var(--backdrop);
    font-family: "Roboto", sans-serif;
    color: var(--ink);
    position: relative;
  }
  .card {
    position: absolute;
    top: 200px;
    width: 540px;
    height: 309px;
    background: var(--card);
    border-radius: 22px;
    overflow: hidden;
    box-shadow: 0 10px 30px rgba(0,0,0,.55);
  }
  .card--front { left: 40px; }
  .card--back { left: 620px; }

  .brand {
    position: absolute;
    display: flex;
    align-items: center;
    gap: 12px;
  }
  .brand__dot {
    width: 22px; height: 22px;
    border-radius: 50%;
    background: var(--ink);
  }
  .brand__name {
    font-weight: 700;
    letter-spacing: .32em;
    color: var(--ink);
  }
  .card--front .brand { left: 50%; top: 50%; transform: translate(-50%, -50%); }
  .card--front .brand__name { font-size: 40px; }

  .card--back .brand { left: 34px; top: 140px; }
  .card--back .brand__dot { width: 16px; height: 16px; }
  .card--back .brand__name { font-size: 27px; }

  .divider {
    position: absolute;
    left: 262px; top: 48px;
    width: 1px; height: 170px;
    background: var(--ink);
  }
  .details {
    position: absolute;
    left: 290px; top: 52px;
    width: 230px;
  }
  .details__name { font-size: 22px; font-weight: 700; line-height: 1.1; }
  .details__role { font-size: 12px; margin-top: 4px; color: var(--muted); }
  .details__tagline { font-size: 11px; line-height: 1.45; margin-top: 12px; color: var(--muted); }
  .contact { list-style: none; margin-top: 14px; font-size: 11px; line-height: 1.45; }
  .contact li { display: flex; gap: 7px; align-items: flex-start; margin-bottom: 3px; }
  .contact svg { flex: none; margin-top: 2px; }
  .band { position: absolute; left: 0; bottom: 0; }
</style>
</head>
<body>
  <section class="card card--front">
    <div class="brand">
      <span class="brand__dot"></span>
      <span class="brand__name">HOPWELL</span>
    </div>
  </section>

  <section class="card card--back">
    <div class="brand">
      <span class="brand__dot"></span>
      <span class="brand__name">HOPWELL</span>
    </div>
    <div class="divider"></div>
    <div class="details">
      <h1 class="details__name">Dalton Pikes</h1>
      <p class="details__role">Founder and CPO</p>
      <p class="details__tagline">If it keeps a drink cold or<br>the party going...we do it!</p>
      <ul class="contact">
        <li>
          <svg width="10" height="10" viewBox="0 0 24 24" fill="#fff"><path d="M6.6 10.8a15.1 15.1 0 0 0 6.6 6.6l2.2-2.2a1 1 0 0 1 1-.25 11.4 11.4 0 0 0 3.6.6 1 1 0 0 1 1 1V20a1 1 0 0 1-1 1A17 17 0 0 1 3 4a1 1 0 0 1 1-1h3.5a1 1 0 0 1 1 1c0 1.25.2 2.45.6 3.6a1 1 0 0 1-.25 1z"/></svg>
          <span>555.318.4726</span>
        </li>
        <li>
          <svg width="10" height="12" viewBox="0 0 20 24" fill="none" stroke="#fff" stroke-width="2"><path d="M10 22s7-7 7-12a7 7 0 0 0-14 0c0 5 7 12 7 12z"/><circle cx="10" cy="10" r="2.5"/></svg>
          <span>412 E. Carver Avenue,<br>Ste 2207, Tampa, FL. 33917</span>
        </li>
      </ul>
    </div>
    <svg class="band" width="540" height="100" viewBox="0 0 540 100">
      <polygon points="0,84 300,84 320,70 330,62 540,62 540,74 338,74 325,82 308,94 0,94" fill="#fff"/>
    </svg>
  </section>
</body>
</html>
```